Heron Loan Partners Business Card

We need a business card design for our mortgage servicing company. In addition to servicing the loans of homeowners, we help homeowners with purchasing their homes and any mortgage refinancing. We would like to see designs that use the colors in the logo attached below (gold-ish yellow and navy blue), and any other design you deem fit! The design should communicate a simpler life with smart mortgages provided by Heron.

```html
<!DOCTYPE html>
<html lang="en">
<head>
<meta charset="utf-8">
<title>Heron Loan Partners Business Card</title>
<link href="https://fonts.googleapis.com/css2?family=Open+Sans:wght@400;600;700&display=swap" rel="stylesheet">
<style>
  :root {
    --navy: #25205a;
    --gold: #e1ad34;
    --white: #ffffff;
    --ink: #4a4a55;
    --backdrop: #7b7b79;
  }
  * { margin: 0; padding: 0; box-sizing: border-box; }
  html, body { width: 1200px; height: 801px; overflow: hidden; }
  body {
    background: var(--backdrop);
    font-family: "Open Sans", Arial, sans-serif;
    position: relative;
  }
  .card {
    position: absolute;
    width: 530px;
    height: 303px;
    overflow: hidden;
    box-shadow: 0 8px 22px rgba(0,0,0,0.25);
  }
  /* Front side */
  .card-front { left: 45px; top: 95px; background: var(--white); border-bottom: 3px solid var(--gold); }
  .front-wave { position: absolute; inset: 0; width: 100%; height: 100%; }
  .front-brand {
    position: absolute; left: 30px; top: 112px; width: 210px;
    display: flex; align-items: center; gap: 10px;
  }
  .brand-dot { width: 14px; height: 14px; border-radius: 50%; background: var(--navy); flex: none; }
  .brand-name { color: var(--gold); font-weight: 700; font-size: 21px; line-height: 1.1; }
  .divider { position: absolute; left: 258px; top: 50px; width: 1px; height: 148px; background: var(--navy); }
  .contact { position: absolute; left: 272px; top: 36px; color: var(--ink); }
  .person-name { color: var(--navy); font-weight: 700; font-size: 17px; letter-spacing: 0.3px; }
  .person-title { color: var(--gold); font-size: 13px; margin-bottom: 10px; }
  .address { font-size: 12.5px; line-height: 1.45; margin-bottom: 10px; }
  .contact-line { display: flex; align-items: center; gap: 8px; font-size: 12.5px; line-height: 1.6; }
  .contact-line svg { width: 10px; height: 10px; fill: var(--gold); flex: none; }
  /* Back side */
  .card-back {
    left: 625px; top: 400px; background: var(--navy);
    border-bottom: 3px solid var(--gold); border-right: 2px solid var(--gold);
    display: flex; align-items: center; justify-content: center; gap: 14px;
  }
  .card-back .brand-dot { background: var(--gold); width: 18px; height: 18px; }
  .card-back .brand-name { font-size: 36px; }
</style>
</head>
<body>
  <section class="card card-front" aria-label="Card front">
    <svg class="front-wave" viewBox="0 0 530 303" preserveAspectRatio="none" aria-hidden="true">
      <path d="M0 284 C170 288 360 272 530 212 L530 303 L0 303 Z" fill="var(--gold)"/>
      <path d="M0 293 C175 296 365 281 530 222 L530 303 L0 303 Z" fill="var(--white)"/>
      <path d="M0 298 C180 300 370 287 530 229 L530 303 L0 303 Z" fill="var(--navy)"/>
    </svg>
    <div class="front-brand">
      <span class="brand-dot"></span>
      <span class="brand-name">Heron Loan Partners</span>
    </div>
    <div class="divider"></div>
    <div class="contact">
      <div class="person-name">DARA WHITFIELD</div>
      <div class="person-title">President</div>
      <div class="address">3172 Cove Landing Way<br>Seabright CA 90412</div>
      <div class="contact-line">
        <svg viewBox="0 0 10 10"><path d="M2 0.5 L4 2.8 L3 4 Q4.5 6 6 7 L7.2 6 L9.5 8 L8 9.6 Q3.5 9 0.4 2 Z"/></svg>
        555-013-4872
      </div>
      <div class="contact-line">
        <svg viewBox="0 0 10 10"><path d="M0 2 H10 V8.5 H0 Z M0.6 2.4 L5 5.6 L9.4 2.4" stroke="#fff" stroke-width="0.8"/></svg>
        info@HeronLoanPartners.com
      </div>
      <div class="contact-line">
        <svg viewBox="0 0 10 10"><circle cx="5" cy="5" r="4.6"/></svg>
        www.HeronLoanPartners.com
      </div>
    </div>
  </section>

  <section class="card card-back" aria-label="Card back">
    <span class="brand-dot"></span>
    <span class="brand-name">Heron Loan Partners</span>
  </section>
</body>
</html>
```